Business Card Design Project

Hi,
This is a simple contest. The logo for the back of the card is deigned. See attached files. The front of the card must have :

Directors Name: Tobias
Mob:
e-mail:
Postal Address:
Web Page Adress:

It may also add words: "Leaders in Construction Project Management Services"

Target Market(s)

Business & Home owners alike

Industry/Entity Type

Business

Requirements
Must have
• See details above and logo attached
Should not have
• Images other than logo

```html
<!DOCTYPE html>
<html lang="en">
<head>
<meta charset="utf-8">
<title>Ridgeline Projects – Business Card</title>
<link rel="stylesheet" href="https://fonts.googleapis.com/css2?family=Raleway:wght@400;500;700&display=swap">
<style>
  :root {
    --backdrop: #ebe6df;
    --brand-blue: #1496d8;
    --brand-blue-deep: #0b86c9;
    --card-grey: #ebebeb;
    --card-white: #f6f6f6;
    --silver-dark: #9a9a9c;
    --silver-light: #f4f4f4;
    --ink-white: #ffffff;
  }
  html, body {
    margin: 0;
    padding: 0;
    width: 1200px;
    height: 923px;
    overflow: hidden;
    background: var(--backdrop);
    font-family: "Raleway", Arial, sans-serif;
  }
  .canvas {
    position: relative;
    width: 1200px;
    height: 923px;
  }
  .card {
    position: absolute;
    width: 656px;
    height: 378px;
    border-radius: 14px;
    overflow: hidden;
    box-shadow: 0 6px 18px rgba(0,0,0,0.18);
  }
  .card-back {
    left: 60px;
    top: 36px;
    background: radial-gradient(ellipse at 45% 45%, #2aa6e6 0%, var(--brand-blue) 55%, var(--brand-blue-deep) 100%);
    display: flex;
    align-items: center;
    justify-content: center;
  }
  .card-front {
    left: 467px;
    top: 425px;
    background: linear-gradient(180deg, var(--card-white) 0%, var(--card-grey) 100%);
  }
  .brand {
    display: flex;
    align-items: center;
    gap: 12px;
    font-weight: 700;
    letter-spacing: 1px;
    text-transform: uppercase;
  }
  .brand-mark {
    width: 30px;
    height: 30px;
  }
  .card-back .brand { color: var(--ink-white); font-size: 30px; }
  .card-back .brand-mark { background: var(--ink-white); }
  .card-front .brand {
    position: absolute;
    left: 0;
    right: 0;
    top: 100px;
    justify-content: center;
    color: var(--brand-blue);
    font-size: 28px;
  }
  .card-front .brand-mark { background: var(--brand-blue); width: 28px; height: 28px; }
  .silver-band {
    position: absolute;
    left: 0;
    right: 0;
    top: 224px;
    height: 21px;
    background: linear-gradient(90deg, var(--silver-dark) 0%, var(--silver-light) 25%, #b5b5b7 50%, var(--silver-light) 75%, var(--silver-dark) 100%);
  }
  .info-panel {
    position: absolute;
    left: 0;
    right: 0;
    top: 245px;
    bottom: 0;
    background: var(--brand-blue);
    color: var(--ink-white);
  }
  .person { position: absolute; left: 31px; top: 12px; }
  .person-name { font-size: 16px; font-weight: 500; letter-spacing: 0.5px; line-height: 1; }
  .person-role { font-size: 11px; margin-top: 2px; }
  .tagline { position: absolute; left: 25px; top: 83px; font-size: 12px; }
  .contacts {
    position: absolute;
    left: 372px;
    top: 9px;
    margin: 0;
    padding: 0;
    list-style: none;
    font-size: 12px;
  }
  .contacts li {
    display: flex;
    align-items: center;
    gap: 19px;
    height: 20.5px;
  }
  .contacts svg { width: 13px; height: 13px; fill: var(--ink-white); flex: none; }
</style>
</head>
<body>
<main class="canvas">
  <section class="card card-back" aria-label="Card back">
    <div class="brand"><span class="brand-mark"></span>Ridgeline Projects</div>
  </section>

  <section class="card card-front" aria-label="Card front">
    <div class="brand"><span class="brand-mark"></span>Ridgeline Projects</div>
    <div class="silver-band"></div>
    <div class="info-panel">
      <div class="person">
        <div class="person-name">TOBIAS</div>
        <div class="person-role">Director</div>
      </div>
      <div class="tagline">Leaders in Construction Project Management Services</div>
      <ul class="contacts">
        <li>
          <svg viewBox="0 0 16 16" aria-hidden="true"><path d="M4 1h8a1 1 0 0 1 1 1v12a1 1 0 0 1-1 1H4a1 1 0 0 1-1-1V2a1 1 0 0 1 1-1zm1 2v8h6V3zm3 9.2a.9.9 0 1 0 0 1.8.9.9 0 0 0 0-1.8z"/></svg>
          041 203 78846
        </li>
        <li>
          <svg viewBox="0 0 16 16" aria-hidden="true"><path d="M1 3h14v10H1zm1.5 1.5L8 8.5l5.5-4z"/></svg>
          tobias@ridgelinepm.com
        </li>
        <li>
          <svg viewBox="0 0 16 16" aria-hidden="true"><path d="M8 1l7 6h-2v8H3V7H1zM6.5 10v5h3v-5z"/></svg>
          PO Box 48 Carlton VIC
        </li>
        <li>
          <svg viewBox="0 0 16 16" aria-hidden="true"><path d="M8 1a7 7 0 1 0 0 14A7 7 0 0 0 8 1zm0 1.5c.9 0 1.8 1.9 2 4.5H6c.2-2.6 1.1-4.5 2-4.5zM2.6 7h2.3c0-1.6.4-3.1.9-4A5.5 5.5 0 0 0 2.6 7zm8.5 0h2.3a5.5 5.5 0 0 0-3.2-4c.5.9.9 2.4.9 4zM2.6 9a5.5 5.5 0 0 0 3.2 4c-.5-.9-.9-2.4-.9-4zm3.4 0c.2 2.6 1.1 4.5 2 4.5s1.8-1.9 2-4.5zm5.1 0c0 1.6-.4 3.1-.9 4a5.5 5.5 0 0 0 3.2-4z"/></svg>
          www.ridgelinepm.com
        </li>
      </ul>
    </div>
  </section>
</main>
</body>
</html>
```